Redesign of business card for Cedar Ridge Mechanical

We are looking for a new design for our business cards for Cedar Ridge Mechanical. We are a plumbing & HVAC construction company, operating on the West Coast of Canada and USA. Logo attached.
Industry/Entity Type
Construction - Plumbing & HVAC
Contact Information for Business Card
Name, address, phone numbers, email, website address
Look and feel
Each slider illustrates characteristics of the customer's brand and the style your logo design should communicate.

```html
<!DOCTYPE html>
<html lang="en">
<head>
<meta charset="utf-8">
<title>Cedar Ridge Mechanical – Business Card</title>
<link href="https://fonts.googleapis.com/css2?family=Poppins:wght@400;500;600&display=swap" rel="stylesheet">
<style>
  :root {
    --backdrop: #6d6d6d;
    --paper: #ffffff;
    --ink: #111111;
    --ink-soft: #3a3a3a;
    --muted: #7a7a7a;
    --stripe: #9a9a9a;
  }
  * { margin: 0; padding: 0; box-sizing: border-box; }
  html, body { width: 1200px; height: 780px; overflow: hidden; }
  body {
    background: var(--backdrop);
    font-family: "Poppins", sans-serif;
    color: var(--ink);
    position: relative;
  }
  .card {
    position: absolute;
    top: 236px;
    width: 530px;
    height: 303px;
    background: var(--paper);
    overflow: hidden;
    box-shadow: 0 10px 24px rgba(0,0,0,.35);
  }
  .card--front { left: 40px; }
  .card--back { left: 630px; display: flex; align-items: center; justify-content: center; }

  .brand { display: flex; align-items: center; gap: 12px; }
  .brand__square { width: 22px; height: 22px; background: var(--ink); flex: none; }
  .brand__name { font-weight: 600; color: var(--ink); line-height: 1.1; }
  .card--back .brand__name { font-size: 30px; width: 240px; }
  .card--back .brand__square { width: 34px; height: 34px; }

  .card--front .brand { position: absolute; left: 34px; top: 70px; }
  .card--front .brand__name { font-size: 20px; width: 160px; }

  .divider { position: absolute; left: 250px; top: 48px; width: 1.5px; height: 160px; background: var(--ink); }

  .contact { position: absolute; left: 272px; top: 50px; }
  .contact__name { font-size: 18px; font-weight: 600; letter-spacing: .3px; }
  .contact__role { font-size: 12.5px; color: var(--muted); margin-top: 1px; }
  .contact__address { font-size: 12.5px; color: var(--ink-soft); margin-top: 10px; line-height: 1.35; }
  .contact__list { list-style: none; margin-top: 10px; font-size: 12.5px; color: var(--ink-soft); line-height: 1.45; }
  .contact__list li { display: flex; align-items: center; gap: 7px; }
  .contact__list svg { width: 11px; height: 11px; flex: none; }

  .wave { position: absolute; left: 0; bottom: 0; width: 530px; height: 303px; }
  .website { position: absolute; left: 80px; bottom: 16px; font-size: 15px; color: var(--paper); letter-spacing: .4px; }
</style>
</head>
<body>

<section class="card card--front">
  <svg class="wave" viewBox="0 0 530 303" aria-hidden="true">
    <path d="M0 150 C60 210 120 262 250 262 C360 262 440 275 530 303 L0 303 Z" fill="var(--stripe)"/>
    <path d="M0 166 C60 228 120 270 250 272 C360 274 440 285 530 303 L0 303 Z" fill="var(--ink)"/>
  </svg>

  <div class="brand">
    <span class="brand__square"></span>
    <span class="brand__name">Cedar Ridge Mechanical</span>
  </div>

  <div class="divider"></div>

  <div class="contact">
    <h1 class="contact__name">DANIEL HAYES</h1>
    <p class="contact__role">Managing Director</p>
    <p class="contact__address">Your address, City<br>State, Zip 1234</p>
    <ul class="contact__list">
      <li><svg viewBox="0 0 12 12"><path d="M3 1 L5 3.5 L4 5 Q5 7 7 8 L8.5 7 L11 9 L9.5 11 Q4 10.5 1 3 Z" fill="var(--ink)"/></svg>123 456 789</li>
      <li><svg viewBox="0 0 12 12"><rect x="3" y="0.5" width="6" height="11" rx="1" fill="none" stroke="var(--ink)" stroke-width="1.2"/><circle cx="6" cy="9.5" r=".7" fill="var(--ink)"/></svg>123 456 789</li>
      <li><svg viewBox="0 0 12 12"><rect x="0.6" y="2.5" width="10.8" height="7.5" fill="none" stroke="var(--ink)" stroke-width="1.2"/><path d="M1 3 L6 7 L11 3" fill="none" stroke="var(--ink)" stroke-width="1.2"/></svg>info@yourmail.com</li>
    </ul>
  </div>

  <p class="website">www.yourwebsite.com</p>
</section>

<section class="card card--back">
  <div class="brand">
    <span class="brand__square"></span>
    <span class="brand__name">Cedar Ridge Mechanical</span>
  </div>
</section>

</body>
</html>
```